Vantor Wear and Fuel is looking for a Clothing/Supplement Online Store Website!

Must be convenient, and user friendly, with vibrant colors that catch the eye!

Target Market(s)

Athletes, and Fashion Customers

Industry/Entity Type

Fitness

Coding

Coded - Design and coding required

Number of Pages Required

3 page

Font styles to use
Decorative

Colors

Designer to choose colors to be used in the design.

Requirements
Must have
• Somewhere to feature products, features to promote discounts and make announcements.
Nice to have
• My logos on each page

```html
<!DOCTYPE html>
<html lang="en">
<head>
<meta charset="utf-8">
<title>Vantor Wear and Fuel</title>
<link href="https://fonts.googleapis.com/css2?family=Michroma&family=Roboto:wght@400;500;700&display=swap" rel="stylesheet">
<style>
:root{
  --ink:#1c1c1c;
  --text:#333;
  --muted:#777;
  --line:#d6d6d6;
  --slate:#555;
  --navy:#363a4a;
  --band:#e9e9e9;
  --white:#fff;
}
*{box-sizing:border-box;margin:0;padding:0}
html,body{width:1200px;height:4095px;overflow:hidden}
body{position:relative;background:var(--white);font-family:"Roboto",Arial,sans-serif;color:var(--text)}
.abs{position:absolute}
.display{font-family:"Michroma","Roboto",sans-serif;font-weight:400;letter-spacing:2px;color:var(--ink)}
.section-title{position:absolute;left:0;width:1200px;text-align:center;font-size:28px}

/* header */
.brand{font-family:"Roboto",sans-serif;font-weight:500;font-size:34px;letter-spacing:1px;color:#3a3a3a;white-space:nowrap}
.call-icon{width:48px;height:48px;border:1px solid var(--line);border-radius:50%;display:flex;align-items:center;justify-content:center}
.call-label{font-size:15px;font-weight:500;color:var(--ink)}
.call-number{font-size:25px;font-weight:500;color:var(--ink)}
.search{left:676px;top:25px;width:278px;height:47px;border:1px solid var(--line);display:flex}
.search span{flex:1;padding:14px 16px;font-size:14px;color:#999}
.search b{width:48px;border-left:1px solid var(--line);display:flex;align-items:center;justify-content:center}
.cart-count{width:22px;height:22px;border:1px solid var(--line);border-radius:50%;font-size:13px;text-align:center;line-height:20px;color:var(--muted);background:#fff}
.nav{display:flex;gap:34px;font-size:15px;font-weight:500;color:var(--ink)}
.nav-marker{width:0;height:0;border-left:9px solid transparent;border-right:9px solid transparent;border-bottom:9px solid var(--slate)}

/* hero */
.hero{left:0;top:158px;width:1200px;height:586px;background:linear-gradient(90deg,#3c3835 0%,#5a4a3a 30%,#2c2a29 55%,#1a1a1a 100%)}
.hero-title{left:570px;top:335px;font-size:38px;line-height:60px;color:#fff;letter-spacing:3px;white-space:nowrap}
.pill{display:inline-flex;align-items:center;gap:12px;height:50px;padding:0 30px;border-radius:25px;border:2px solid var(--slate);background:#fff;font-size:15px;font-weight:500;color:var(--ink)}
.arrow-btn{width:46px;height:46px;border-radius:50%;background:#fff;display:flex;align-items:center;justify-content:center}

/* perks */
.perk{top:852px;width:315px;height:120px;border:1px solid var(--line);display:flex}
.perk-icon{width:88px;background:var(--slate);display:flex;align-items:center;justify-content:center}
.perk-body{padding:18px 0 0 22px}
.perk-body h4{font-size:15px;font-weight:500;color:var(--ink);margin-bottom:10px}
.perk-body p{font-size:15px;line-height:26px;color:var(--muted)}

/* featured */
.soft-band{left:0;width:1200px;background:linear-gradient(135deg,#efefef,#f6f6f6 50%,#ebebeb)}
.card{position:absolute;background:#fff;box-shadow:0 0 10px rgba(0,0,0,.12)}
.shot{position:absolute;border-radius:6px}
.prod-name{position:absolute;left:20px;top:296px;font-size:16px;font-weight:500;color:var(--ink)}
.prod-price{position:absolute;left:20px;top:326px;font-size:23px;font-weight:500;color:var(--text)}
.prod-price s{margin-right:18px;color:#555}
.cart-btn{position:absolute;right:20px;top:296px;width:46px;height:46px;border:2px solid var(--slate);display:flex;align-items:center;justify-content:center}
.cart-btn.solid{background:var(--slate)}

/* promo */
.promo-photo{left:113px;top:1820px;width:500px;height:289px;background:linear-gradient(90deg,#5c5852,#8b7562 45%,#4a4a4e)}
.promo-panel{left:613px;top:1820px;width:476px;height:289px;background:var(--navy);color:#fff;padding:42px 16px 0 23px}
.promo-panel h3{font-size:34px;font-weight:700;margin-bottom:14px}
.promo-panel p{font-size:15px;line-height:26px;color:#e3e4ea;margin-bottom:20px}

/* best sales */
.sale-price{font-size:25px;font-weight:500;color:var(--ink)}
.sale-price s{margin-right:30px}
.sale-name{font-size:18px;font-weight:500;color:var(--ink);margin:22px 0 14px}
.sale-copy{font-size:15px;line-height:26px;color:var(--muted)}

/* blog */
.post-date{font-size:17px;color:var(--muted);display:flex;align-items:center;gap:12px}
.post-title{font-size:17px;font-weight:500;color:var(--ink);margin:22px 0 14px}

/* newsletter & footer */
.field{left:334px;top:3773px;width:372px;height:49px;border:1px solid #bbb;background:#fff;display:flex;align-items:center;gap:12px;padding-left:22px;font-size:15px;color:#666}
.subscribe{left:706px;top:3773px;width:160px;height:49px;background:var(--slate);color:#fff;font-size:16px;font-weight:700;display:flex;align-items:center;justify-content:center}
.foot-nav{display:flex;gap:30px;font-size:15px;font-weight:500;color:var(--ink)}
.social{width:46px;height:46px;border:2px solid var(--slate);border-radius:50%}
</style>
</head>
<body>

<!-- header -->
<div class="abs brand" style="left:113px;top:52px">WEAR &amp; FUEL</div>
<div class="abs call-icon" style="left:394px;top:26px">
  <svg width="22" height="22" viewBox="0 0 24 24"><path fill="#555" d="M6.6 10.8a15.1 15.1 0 0 0 6.6 6.6l2.2-2.2c.3-.3.7-.4 1-.2 1.1.4 2.3.6 3.6.6.6 0 1 .4 1 1V20c0 .6-.4 1-1 1A17 17 0 0 1 3 4c0-.6.4-1 1-1h3.5c.6 0 1 .4 1 1 0 1.3.2 2.5.6 3.6.1.3 0 .7-.2 1z"/></svg>
</div>
<div class="abs call-label" style="left:461px;top:24px">CALL US TODAY</div>
<div class="abs call-number" style="left:461px;top:46px">800 555 0142</div>
<div class="abs search"><span>Search</span><b><svg width="20" height="20" viewBox="0 0 24 24"><circle cx="10" cy="10" r="7" fill="none" stroke="#444" stroke-width="2.6"/><path d="M15 15l6 6" stroke="#444" stroke-width="2.8"/></svg></b></div>
<svg class="abs" style="left:1006px;top:36px" width="30" height="28" viewBox="0 0 24 22"><path fill="#555" d="M0 1h4l1 3h18l-3 9H7l-1 2h15v2H3l2-5L2 3H0z"/><circle cx="8" cy="19.5" r="2" fill="#555"/><circle cx="19" cy="19.5" r="2" fill="#555"/></svg>
<div class="abs cart-count" style="left:1032px;top:24px">0</div>
<nav class="abs nav" style="left:433px;top:112px"><span>HOME</span><span>ABOUT US</span><span>OUR PRODUCTS</span><span>BLOG</span><span>CONTACT US</span><span>REVIEWS</span></nav>
<div class="abs nav-marker" style="left:448px;top:149px"></div>

<!-- hero -->
<div class="abs hero" role="img" aria-label="Athlete in a gym drinking from a shaker bottle"></div>
<div class="abs display hero-title">VANTOR WEAR<br>AND FUEL</div>
<div class="abs pill" style="left:570px;top:487px">SHOP NOW
  <svg width="16" height="14" viewBox="0 0 24 22"><path fill="#555" d="M0 1h4l1 3h18l-3 9H7l-1 2h15v2H3l2-5L2 3H0z"/><circle cx="8" cy="19.5" r="2" fill="#555"/><circle cx="19" cy="19.5" r="2" fill="#555"/></svg></div>
<div class="abs arrow-btn" style="left:31px;top:428px"><svg width="16" height="16" viewBox="0 0 16 16"><path d="M10 2L4 8l6 6" fill="none" stroke="#222" stroke-width="2.2"/></svg></div>
<div class="abs arrow-btn" style="left:1121px;top:428px"><svg width="16" height="16" viewBox="0 0 16 16"><path d="M6 2l6 6-6 6" fill="none" stroke="#222" stroke-width="2.2"/></svg></div>

<!-- perks -->
<div class="abs perk" style="left:112px">
  <div class="perk-icon"><svg width="58" height="50" viewBox="0 0 58 50" fill="none" stroke="#fff" stroke-width="2"><rect x="4" y="16" width="32" height="22" rx="2"/><path d="M36 22h10l8 8v8H36z"/><circle cx="14" cy="42" r="4"/><circle cx="46" cy="42" r="4"/><path d="M14 16V6h12v10M20 6V2"/></svg></div>
  <div class="perk-body"><h4>FREE SHIPPING</h4><p>Lorem ipsum dolor sit<br>amet, consectetur.</p></div>
</div>
<div class="abs perk" style="left:443px">
  <div class="perk-icon"><svg width="56" height="44" viewBox="0 0 56 44" fill="none" stroke="#fff" stroke-width="2"><rect x="4" y="8" width="48" height="30" rx="3"/><path d="M4 18h48M20 8v30"/><path d="M20 18c-6-8-12-2-6 0M20 18c6-8 12-2 6 0"/><path d="M30 30h16"/></svg></div>
  <div class="perk-body"><h4>BUY A GIFT CARD</h4><p>Lorem ipsum dolor sit<br>amet, consectetur.</p></div>
</div>
<div class="abs perk" style="left:773px">
  <div class="perk-icon"><svg width="54" height="54" viewBox="0 0 54 54" fill="none" stroke="#fff" stroke-width="2"><path d="M27 3l6 5 8-1 2 8 7 4-3 7 3 7-7 4-2 8-8-1-6 5-6-5-8 1-2-8-7-4 3-7-3-7 7-4 2-8 8 1z"/><circle cx="21" cy="21" r="3.5"/><circle cx="33" cy="33" r="3.5"/><path d="M35 19L19 35"/></svg></div>
  <div class="perk-body"><h4>SEASON SALE 20% OFF</h4><p>Lorem ipsum dolor sit<br>amet, consectetur.</p></div>
</div>

<!-- featured products -->
<div class="abs soft-band" style="top:1071px;height:657px" role="img" aria-label="Faded background of fitness food and drinks"></div>
<h2 class="display section-title" style="top:1132px">FEATURED PRODUCTS</h2>

<div class="card" style="left:109px;top:1246px;width:304px;height:390px">
  <div class="shot" style="left:65px;top:40px;width:175px;height:195px;background:linear-gradient(180deg,#2a2a2a,#111)" role="img" aria-label="Black leather biker jacket"></div>
  <div class="prod-name">ET HARUM QUIDEM ET</div>
  <div class="prod-price">$ 1,500</div>
  <div class="cart-btn"><svg width="20" height="18" viewBox="0 0 24 22"><path fill="#555" d="M0 1h4l1 3h18l-3 9H7l-1 2h15v2H3l2-5L2 3H0z"/><circle cx="8" cy="19.5" r="2" fill="#555"/><circle cx="19" cy="19.5" r="2" fill="#555"/></svg></div>
</div>
<div class="card" style="left:446px;top:1246px;width:304px;height:390px;overflow:hidden">
  <div class="shot" style="left:104px;top:40px;width:96px;height:172px;border-radius:18px;background:linear-gradient(90deg,#111,#4a4a4a 40%,#111)" role="img" aria-label="Black supplement tub"></div>
  <svg class="abs" style="right:0;top:0" width="104" height="104" viewBox="0 0 104 104"><path d="M0 0h104v104z" fill="var(--slate)"/><text x="68" y="40" fill="#fff" font-family="Roboto,sans-serif" font-weight="700" font-size="26">%</text></svg>
  <div class="prod-name">ET HARUM QUIDEM ET</div>
  <div class="prod-price"><s>$ 1,500</s>$ 1,100</div>
  <div class="cart-btn solid"><svg width="20" height="18" viewBox="0 0 24 22"><path fill="#fff" d="M0 1h4l1 3h18l-3 9H7l-1 2h15v2H3l2-5L2 3H0z"/><circle cx="8" cy="19.5" r="2" fill="#fff"/><circle cx="19" cy="19.5" r="2" fill="#fff"/></svg></div>
</div>
<div class="card" style="left:783px;top:1246px;width:304px;height:390px">
  <div class="shot" style="left:100px;top:40px;width:104px;height:198px;background:linear-gradient(180deg,#c2182b 0 22%,#111 22%)" role="img" aria-label="Black and red training tank top"></div>
  <div class="prod-name">ET HARUM QUIDEM ET</div>
  <div class="prod-price">$ 1,500</div>
  <div class="cart-btn"><svg width="20" height="18" viewBox="0 0 24 22"><path fill="#555" d="M0 1h4l1 3h18l-3 9H7l-1 2h15v2H3l2-5L2 3H0z"/><circle cx="8" cy="19.5" r="2" fill="#555"/><circle cx="19" cy="19.5" r="2" fill="#555"/></svg></div>
</div>

<!-- promo -->
<div class="abs promo-photo" role="img" aria-label="Athlete sitting on a gym bench drinking a protein shake"></div>
<div class="abs promo-panel">
  <h3>GET 10% OFF</h3>
  <p>Et harum quidem rerum facilis est et expedita distinctio. Nam libero tempore, cum soluta nobis est eligendi optio cumque nihil impedit quo minus id quod maxime.</p>
  <div class="pill">SHOP NOW <svg width="16" height="14" viewBox="0 0 24 22"><path fill="#555" d="M0 1h4l1 3h18l-3 9H7l-1 2h15v2H3l2-5L2 3H0z"/><circle cx="8" cy="19.5" r="2" fill="#555"/><circle cx="19" cy="19.5" r="2" fill="#555"/></svg></div>
</div>

<!-- best sales -->
<div class="abs soft-band" style="top:2201px;height:736px" role="img" aria-label="Faded background of a woman with fitness gear"></div>
<h2 class="display section-title" style="top:2272px">BEST SALES</h2>

<div class="card" style="left:111px;top:2397px;width:313px;height:408px;padding:250px 34px 0">
  <div class="shot" style="left:106px;top:30px;width:100px;height:185px;border-radius:18px;background:linear-gradient(90deg,#111,#4a4a4a 40%,#111)" role="img" aria-label="Black supplement tub"></div>
  <div class="sale-price">$ 3,000</div>
  <div class="sale-name">LOREM IPSUM DOLOR</div>
  <div class="sale-copy">Excepteur sint occaecat cupidatat non proident, sunt in culpa.</div>
</div>
<div class="card" style="left:443px;top:2362px;width:312px;height:478px;padding:240px 34px 0">
  <div class="shot" style="left:86px;top:30px;width:136px;height:165px;background:linear-gradient(180deg,#333,#111)" role="img" aria-label="Black hooded sweatshirt"></div>
  <svg class="abs" style="left:222px;top:22px" width="76" height="58" viewBox="0 0 76 58"><path d="M38 2l7 7 10-4 2 10 12 2-5 9 8 8-11 4 1 11-11-3-6 9-7-9-11 3 1-11-11-4 8-8-5-9 12-2 2-10 10 4z" fill="var(--slate)"/><text x="38" y="34" text-anchor="middle" fill="#fff" font-family="Roboto,sans-serif" font-weight="700" font-size="13">SALE</text></svg>
  <div class="sale-price"><s>$ 5,000</s>$ 3,000</div>
  <div class="sale-name">LOREM IPSUM DOLOR</div>
  <div class="sale-copy">Excepteur sint occaecat cupidatat non proident, sunt in culpa.</div>
  <div class="pill" style="margin-top:20px">SHOP NOW <svg width="16" height="14" viewBox="0 0 24 22"><path fill="#555" d="M0 1h4l1 3h18l-3 9H7l-1 2h15v2H3l2-5L2 3H0z"/><circle cx="8" cy="19.5" r="2" fill="#555"/><circle cx="19" cy="19.5" r="2" fill="#555"/></svg></div>
</div>
<div class="card" style="left:774px;top:2397px;width:313px;height:408px;padding:250px 34px 0">
  <div class="shot" style="left:106px;top:30px;width:100px;height:185px;border-radius:18px;background:linear-gradient(90deg,#111,#4a4a4a 40%,#111)" role="img" aria-label="Black supplement tub"></div>
  <div class="sale-price">$ 3,000</div>
  <div class="sale-name">LOREM IPSUM DOLOR</div>
  <div class="sale-copy">Excepteur sint occaecat cupidatat non proident, sunt in culpa.</div>
</div>

<!-- latest blog -->
<h2 class="display section-title" style="top:3024px">LATEST BLOG</h2>

<div class="card" style="left:111px;top:3138px;width:312px;height:382px">
  <div class="shot" style="left:2px;top:2px;width:308px;height:196px;border-radius:0;background:linear-gradient(135deg,#4a4d5c,#8a6f79 50%,#3e4150)" role="img" aria-label="Clothing store with mannequins in sportswear"></div>
  <div class="abs" style="left:28px;top:222px;right:20px">
    <div class="post-date"><svg width="16" height="16" viewBox="0 0 16 16" fill="none" stroke="#777" stroke-width="1.5"><rect x="1" y="3" width="14" height="12"/><path d="M1 7h14M5 1v4M11 1v4"/></svg>20 October 2019</div>
    <div class="post-title">VOLUPTATEM ACCUSANTIUM</div>
    <div class="sale-copy">Sed ut perspiciatis unde omnis iste natus error sit voluptatem</div>
  </div>
</div>
<div class="card" style="left:443px;top:3138px;width:312px;height:382px">
  <div class="shot" style="left:2px;top:2px;width:308px;height:196px;border-radius:0;background:linear-gradient(135deg,#f0ece6,#d8b59a 50%,#b5573e)" role="img" aria-label="Protein shakers, eggs and meat on a table"></div>
  <div class="abs" style="left:28px;top:222px;right:20px">
    <div class="post-date"><svg width="16" height="16" viewBox="0 0 16 16" fill="none" stroke="#777" stroke-width="1.5"><rect x="1" y="3" width="14" height="12"/><path d="M1 7h14M5 1v4M11 1v4"/></svg>20 October 2019</div>
    <div class="post-title">VOLUPTATEM ACCUSANTIUM</div>
    <div class="sale-copy">Sed ut perspiciatis unde omnis iste natus error sit voluptatem</div>
  </div>
</div>
<div class="card" style="left:774px;top:3138px;width:312px;height:382px">
  <div class="shot" style="left:2px;top:2px;width:308px;height:196px;border-radius:0;background:linear-gradient(135deg,#6b5a4c,#3b4d6a 50%,#a08672)" role="img" aria-label="Fashion store interior with displayed outfits"></div>
  <div class="abs" style="left:28px;top:222px;right:20px">
    <div class="post-date"><svg width="16" height="16" viewBox="0 0 16 16" fill="none" stroke="#777" stroke-width="1.5"><rect x="1" y="3" width="14" height="12"/><path d="M1 7h14M5 1v4M11 1v4"/></svg>20 October 2019</div>
    <div class="post-title">VOLUPTATEM ACCUSANTIUM</div>
    <div class="sale-copy">Sed ut perspiciatis unde omnis iste natus error sit voluptatem</div>
  </div>
</div>

<!-- newsletter & footer -->
<div class="abs" style="left:0;top:3608px;width:1200px;height:487px;background:var(--band)"></div>
<h2 class="display section-title" style="top:3694px">JOIN OUR NEWSLETTER</h2>
<div class="abs field"><svg width="18" height="14" viewBox="0 0 18 14" fill="none" stroke="#666" stroke-width="1.5"><rect x="1" y="1" width="16" height="12"/><path d="M1 1l8 7 8-7"/></svg>Enter Your Email</div>
<div class="abs subscribe">SUBSCRIBE</div>

<div class="abs brand" style="left:113px;top:3854px;font-size:30px">WEAR &amp; FUEL</div>
<p class="abs" style="left:113px;top:3896px;width:232px;font-size:15px;line-height:26px;color:var(--text);text-align:justify">Temporibus autem quibusdam et aut officiis debitis aut rerum necessitatibus saepe.</p>
<div class="abs" style="left:113px;top:4005px;display:flex;gap:12px"><div class="social"></div><div class="social"></div><div class="social"></div><div class="social"></div></div>
<nav class="abs foot-nav" style="left:496px;top:3910px"><span>HOME</span><span>ABOUT US</span><span>OUR PRODUCTS</span><span>BLOG</span><span>CONTACT US</span><span>REVIEWS</span></nav>
<div class="abs" style="left:496px;top:3960px;width:588px;height:1px;background:#999"></div>
<div class="abs" style="left:496px;top:3993px;font-size:16px;color:var(--ink)">© 2019 Vantor Wear and Fuel. All Rights Reserved</div>

</body>
</html>
```